Vorn upkeep KT Solar Venture

Solar power system install
Services and maintenance
wiring, Rewinding and Renovation
Switch Board Upgrade
Power and lighting point
t doesn’t matter how much you spend on quality parts, your solar system will let you down if your design and installation are sub-par. Have your solar system tailored and installed by our Master Electrician and Bright Grid Guild Accredited team.

Target Market(s)

sales and installed

Industry/Entity Type

Solar install and retailer

Contact Information for Business Card

Name , Email, Phone Number ,Business address,

Font styles to use
Serif

Colors
0054AA
0677BA
7BADD7
CADEEF
E8F1F8

Requirements
Must have
• clear and bright
Nice to have
• new design
Should not have
• unclear pictures

```html
<!DOCTYPE html>
<html lang="en">
<head>
<meta charset="utf-8">
<title>Vorn upkeep KT Solar Venture – Business Card</title>
<link rel="stylesheet" href="https://fonts.googleapis.com/css2?family=Roboto:wght@400;500;700&display=swap">
<style>
  :root {
    --stage: #2e2f31;
    --blue-deep: #0054aa;
    --blue-mid: #0677ba;
    --blue-soft: #7badd7;
    --blue-pale: #cadeef;
    --blue-mist: #e8f1f8;
    --teal: #1f8ea0;
    --green: #6ab33e;
    --green-deep: #3fa63a;
    --sun: #f3b51b;
    --ink: #1c1c1c;
    --silver: #e3e3e3;
    --white: #ffffff;
  }
  * { box-sizing: border-box; margin: 0; padding: 0; }
  html, body {
    width: 1200px; height: 1138px; overflow: hidden;
    background: var(--stage);
    font-family: "Roboto", Arial, sans-serif;
  }
  .card {
    position: absolute;
    border-radius: 14px;
    overflow: hidden;
  }

  /* Front */
  .card-front {
    left: 274px; top: 186px; width: 622px; height: 376px;
    background: linear-gradient(115deg, var(--blue-mid) 0%, var(--teal) 45%, var(--green) 100%);
  }
  .brand {
    position: absolute; display: flex; align-items: center;
  }
  .brand-mark {
    border-radius: 50%;
    background: var(--sun);
    flex: none;
  }
  .front-brand { left: 102px; top: 66px; }
  .front-brand .brand-mark { width: 104px; height: 104px; margin-right: 32px; }
  .brand-name {
    font-weight: 700; text-transform: uppercase; line-height: 1.05;
    letter-spacing: 0.5px;
  }
  .front-brand .brand-name { color: var(--white); font-size: 32px; }
  .service-band {
    position: absolute; left: 0; top: 238px; width: 100%; height: 74px;
    background: linear-gradient(180deg, #f2f2f2, #d9d9d9);
    display: flex; flex-direction: column; justify-content: center; align-items: center;
    color: var(--ink); font-size: 15.5px; line-height: 23px;
  }
  .web-line {
    position: absolute; left: 0; top: 331px; width: 100%;
    display: flex; justify-content: center; align-items: center;
    color: var(--blue-mist); font-size: 15px;
  }
  .web-line::before, .web-line::after {
    content: ""; width: 80px; height: 1.5px; background: var(--blue-pale);
    margin: 0 24px;
  }

  /* Back */
  .card-back {
    left: 276px; top: 608px; width: 618px; height: 374px;
    background: linear-gradient(180deg, #f6f6f6, #e9e9e9);
  }
  .back-brand {
    left: 20px; top: 110px; width: 276px;
    flex-direction: column; text-align: center;
  }
  .back-brand .brand-mark { width: 100px; height: 100px; margin-bottom: 18px; }
  .back-brand .brand-name { color: var(--blue-deep); font-size: 25px; }
  .contact {
    position: absolute; left: 344px; top: 74px; color: var(--ink);
  }
  .contact-name { color: var(--blue-deep); font-size: 26px; font-weight: 500; line-height: 32px; }
  .contact-role { font-size: 16px; line-height: 22px; }
  .contact-address { font-size: 16px; line-height: 24px; margin-top: 24px; }
  .contact-list { list-style: none; margin-top: 6px; font-size: 16px; line-height: 24px; }
  .contact-list li { display: flex; align-items: center; }
  .contact-list svg { width: 14px; height: 14px; margin: 0 17px 0 2px; fill: var(--green-deep); }
  .green-strip {
    position: absolute; left: 0; bottom: 0; width: 300px; height: 14px;
    background: linear-gradient(90deg, var(--green), var(--green-deep));
  }
  .tag-tab {
    position: absolute; right: 0; bottom: 0; width: 350px; height: 46px;
    background: var(--blue-mid);
    clip-path: polygon(24px 0, 100% 0, 100% 100%, 0 100%);
    color: var(--blue-mist); font-size: 16px;
    padding-left: 76px; line-height: 46px;
  }
</style>
</head>
<body>
  <section class="card card-front">
    <div class="brand front-brand">
      <span class="brand-mark"></span>
      <span class="brand-name">Vorn Upkeep<br>KT Solar Venture</span>
    </div>
    <div class="service-band">
      <p>Solar Power System Install &nbsp;|&nbsp; Wiring, Rewinding &amp; Renovation</p>
      <p>Services &amp; Maintenance &nbsp;|&nbsp; Switch Board Upgrade &nbsp;|&nbsp; Power &amp; Lighting Point</p>
    </div>
    <p class="web-line">www.ktsolarventure.com</p>
  </section>

  <section class="card card-back">
    <div class="brand back-brand">
      <span class="brand-mark"></span>
      <span class="brand-name">Vorn Upkeep<br>KT Solar Venture</span>
    </div>
    <div class="contact">
      <p class="contact-name">Dana Lee Moore</p>
      <p class="contact-role">Managing Director</p>
      <p class="contact-address">58 Harbor Lane, Eastfield,<br>Brookvale, US 482910</p>
      <ul class="contact-list">
        <li><svg viewBox="0 0 16 16"><path d="M3 2h3l1.5 3.5-2 1.3a9 9 0 0 0 3.7 3.7l1.3-2L14 10v3a1 1 0 0 1-1 1A11 11 0 0 1 2 3a1 1 0 0 1 1-1z"/></svg>555-204-7788</li>
        <li><svg viewBox="0 0 16 16"><path d="M1 3h14v10H1z M2 4l6 5 6-5" fill="none" stroke="#3fa63a" stroke-width="1.6"/></svg>dana@ktsolarventure.com</li>
        <li><svg viewBox="0 0 16 16"><circle cx="8" cy="8" r="6.5" fill="none" stroke="#3fa63a" stroke-width="1.4"/><path d="M1.5 8h13M8 1.5c-3 3.5-3 9.5 0 13M8 1.5c3 3.5 3 9.5 0 13" fill="none" stroke="#3fa63a" stroke-width="1.2"/></svg>www.ktsolarventure.com</li>
      </ul>
    </div>
    <span class="green-strip"></span>
    <p class="tag-tab">Solar power system install</p>
  </section>
</body>
</html>
```